High-end law practice specializing in closely held business succession planning and complex estates

Solo practitioner whose practice specializes in high-net worth, complex estate planning needs muliple versions of letterhead black and white, please. Letterhead should incorporate slogan, "Guarding the legacy your family has built," for one and "Complex Estate Planning"; third with no slogan. All for The Law Office of Marcy Lynn Pettibone, PC, 418 Cedar Hollow Ln., Larkmoor Bay, Calverton 23648, Tel. 555-555-0142 Fax tbd email: marcy@mlplawgroup.example; Marcy Lynn Pettibone, Esq., principal, licensed in VA, NY, DC
Updates

Project Deadline Extended
Reason: My internet service went down and I can only view designs on my smart phone -- it's just too hard to review. So sorry! Working with my ISP now. Please be patient!

Target Market(s)

High net worth clients with complex estate planning needs, family businesses, family farmers, family foresters -- people with unique estate/succession planning needs who need a specialist who understands them.

Industry/Entity Type

Business

Font styles to use
Script

Requirements
Must have
• A high-end look and feel, connoting trustworthiness, special knowledge, and expertise.

```html
<!DOCTYPE html>
<html lang="en">
<head>
<meta charset="utf-8">
<title>Marcy Lynn Pettibone – Letterhead</title>
<link rel="stylesheet" href="https://fonts.googleapis.com/css2?family=Cinzel:wght@600&family=Source+Sans+3:wght@400;500&family=Questrial&display=swap">
<style>
  :root {
    --backdrop: #dcdcdc;
    --paper: #ffffff;
    --brand-blue: #24557f;
    --band-grey: #4f4d4e;
    --ink: #161616;
    --ink-soft: #3a3a3a;
  }
  html, body {
    margin: 0;
    width: 1200px;
    height: 900px;
    overflow: hidden;
    background: var(--backdrop);
  }
  .letterhead {
    position: absolute;
    left: 302px;
    top: 70px;
    width: 599px;
    height: 761px;
    background: var(--paper);
    font-family: "Source Sans 3", "Myriad Pro", sans-serif;
    color: var(--ink);
  }
  .side-band {
    position: absolute;
    left: 0;
    top: 0;
    width: 26px;
    height: 761px;
  }
  .brand {
    position: absolute;
    left: 64px;
    top: 36px;
    display: flex;
    align-items: center;
  }
  .brand-square {
    width: 66px;
    height: 66px;
    background: var(--brand-blue);
  }
  .brand-rule {
    width: 2px;
    height: 82px;
    background: var(--brand-blue);
    margin: 0 8px 0 9px;
  }
  .brand-name {
    font-family: "Cinzel", "Trajan Pro", serif;
    font-weight: 600;
    font-size: 20px;
    line-height: 24px;
    color: var(--brand-blue);
    letter-spacing: 0.2px;
  }
  .contact {
    position: absolute;
    left: 415px;
    top: 35px;
    border-left: 2px solid var(--brand-blue);
    padding-left: 6px;
    font-size: 9.3px;
    line-height: 10.6px;
    color: var(--ink-soft);
    font-style: normal;
    height: 76px;
  }
  .contact-line {
    display: flex;
    align-items: center;
    gap: 4px;
  }
  .contact-line svg { width: 8px; height: 8px; flex: none; }
  .contact-address { margin-top: 5px; }
  .letter {
    position: absolute;
    left: 57px;
    top: 192px;
    width: 493px;
    font-size: 10.7px;
    line-height: 16.9px;
    font-weight: 500;
  }
  .salutation { margin: 0 0 17px 2px; font-size: 11px; }
  .letter p.body {
    margin: 0 0 16px 0;
    text-align: justify;
    text-indent: 2px;
  }
  .signature {
    position: absolute;
    left: 58px;
    top: 560px;
    width: 178px;
    height: 50px;
    background: linear-gradient(90deg, #e9e9e9, #f4f4f4);
  }
  .sign-title {
    position: absolute;
    left: 59px;
    top: 616px;
    margin: 0;
    font-family: "Questrial", "Century Gothic", sans-serif;
    font-size: 11.5px;
    color: var(--ink-soft);
  }
  .slogan {
    position: absolute;
    left: 26px;
    right: 0;
    top: 720px;
    margin: 0;
    text-align center;
    text-align: center;
    font-family: "Cinzel", "Trajan Pro", serif;
    font-weight: 600;
    font-size: 11.5px;
    letter-spacing: 0.4px;
    color: var(--brand-blue);
  }
</style>
</head>
<body>
<main class="letterhead">
  <svg class="side-band" viewBox="0 0 26 761" aria-hidden="true">
    <polygon points="0,0 26,0 26,108 0,133" fill="var(--band-grey)"/>
    <polygon points="0,146 26,121 26,761 0,761" fill="var(--brand-blue)"/>
  </svg>

  <header class="brand">
    <div class="brand-square"></div>
    <div class="brand-rule"></div>
    <div class="brand-name">Marcy Lynn<br>Pettibone</div>
  </header>

  <address class="contact">
    <div class="contact-line">
      <svg viewBox="0 0 8 8"><rect width="8" height="8" rx="1" fill="var(--brand-blue)"/><path d="M2 2 L3 2 L3.6 3.4 L3 4 Q3.8 5 4.6 5.4 L5.2 4.8 L6.4 5.4 L6.2 6.4 Q3 6.4 1.8 3 Z" fill="#fff"/></svg>
      <span>555-555-0142</span>
    </div>
    <div class="contact-line">
      <svg viewBox="0 0 8 8"><rect x="1" y="3" width="6" height="4" fill="var(--brand-blue)"/><rect x="2.2" y="0.8" width="3.6" height="2.4" fill="var(--brand-blue)"/></svg>
      <span>555-555-0142</span>
    </div>
    <div class="contact-line">
      <svg viewBox="0 0 8 8"><rect y="1.5" width="8" height="5" fill="var(--brand-blue)"/><path d="M0 1.5 L4 4.5 L8 1.5" stroke="#fff" stroke-width="0.8" fill="none"/></svg>
      <span>marcy@mlplawgroup.example</span>
    </div>
    <div class="contact-line">
      <svg viewBox="0 0 8 8"><ellipse cx="4" cy="4" rx="4" ry="3" fill="#9aa6b3"/></svg>
      <span>www.mlplawgroup.example</span>
    </div>
    <div class="contact-address">PC, 418 Cedar Hollow Ln., Larkmoor Bay,<br>Calverton 23648</div>
  </address>

  <section class="letter">
    <p class="salutation">Dear Client</p>
    <p class="body">Lorem ipsum dolor sit amet, consectetur adipiscing elit. Pellentesque semper purus ornare dolor eleifend aliquam. Integer molestie gravida sem a porttitor. Quisque pulvinar tellus ut ipsum molestie ultricies id non turpis. Phasellus feugiat ornare feugiat. Integer nec velit eu justo laoreet condimentum. Aenean non commodo quam. Phasellus lacinia aliquet turpis. Praesent non elit nec ante porta cursus. Morbi et augue enim, nec ultrices augue. Etiam tempus arcu laoreet metus tristique ultrices.</p>
    <p class="body">Curabitur nec venenatis risus. Integer nec nisi sit amet leo mattis aliquam. Vivamus vulputate tellus quis purus lobortis rutrum. Aenean nec ipsum ut mauris faucibus facilisis vel porttitor neque. Morbi molestie magna id neque scelerisque ut iaculis justo porttitor. Sed est ligula, semper at cursus ac, porttitor ac ipsum. Maecenas pulvinar euismod tempor. Pellentesque habitant morbi tristique senectus et netus et malesuada fames ac turpis egestas. Integer nec velit turpis. Aliquam adipiscing massa sed ipsum commodo id ullamcorper leo volutpat. Sed vitae tellus dui.</p>
    <p class="body">Maecenas vel neque ante, id faucibus ipsum. Suspendisse non neque quis nunc rhoncus bibendum. Fusce sit amet quam quis libero facilisis ultrices. Donec dignissim lorem vel sem sodales mollis. Duis nec sem lorem, at tristique nibh. In rutrum fermentum lectus, nec dictum leo tincidunt in. Nam metus odio, molestie a tempor a, laoreet placerat dui. Fusce sit amet nisi at elit bibendum imperdiet. Sed fringilla nisi non nunc facilisis in ullamcorper justo suscipit. Fusce fermentum tincidunt sagittis.</p>
  </section>

  <div class="signature" role="img" aria-label="Handwritten signature of the managing director"></div>
  <p class="sign-title">Managing Director</p>

  <p class="slogan">Guarding the legacy your family has built</p>
</main>
</body>
</html>
```